Metal Fabrication Business Official Opening Party Invitation

We need a postcard designed to promote the official opening celebration of our business.

Dimensions can be:
148mm x 105mm OR 210 x 148mm
Flat card please - not folded - CAN be double sided if that suits your design better

We are a metal fabrication business which designs, engineers, repairs and manufactures a range of custom, quality metal works including vehicle trays, agricultural machinery implements, trailers, wood splitters, fire pits, furniture etc.
The brand position focuses on custom work of the highest quality.
The design for this piece should be INDUSTRIAL, (prefer a darker perhaps metal background) whilst still being fun and semi rustic. It's a party after all - but a party about metal. It will be winter so it's OK to have a "cold" feel - one of our products are firepits.

If you have questions or would like more specific information please ask.

Branding guidelines are attached. Feel free to go outside of these guidelines to add more creativity and fun to this particular design

Also attached some invited we found online that we like some parts of - VERY open to ideas and creativity, just as a bit of an idea what we like :) We'd LOVE something original and creative.
Updates

Target Market(s)

Males aged 30 - 60yrs
Country area - farmers and tradespeople

Industry/Entity Type

Business

Requirements
Must have
• Must be a unique, industrial (steel/metal) theme.
• Can include things like cogs/gears, screws etc in the design.
• see the attached 'invite likes..." also
• Text to be included in design include:
• Harlow Ironworks (can just use logo) official opening
• Date: Fri Aug 26
• Location: 5678 Road label
• Time: 6:00pm
• "Join us to celebrate the official opening of Harlow Ironworks"
• Light dinner provided
Should not have
• NO SHINY METAL FINISHES PLEASE

```html
<!DOCTYPE html>
<html lang="en">
<head>
<meta charset="utf-8">
<title>Harlow Ironworks – Official Opening Invitation</title>
<link rel="stylesheet" href="https://fonts.googleapis.com/css2?family=Oswald:wght@400;500;600&display=swap">
<style>
  :root {
    --navy: #1c2a55;
    --white: #ffffff;
    --steel-dark: #1f2a33;
    --steel-mid: #5f7686;
    --steel-light: #b9cbd6;
    --steel-blue: #2f5a86;
    --name-grey: #c9cdd1;
    --accent-green: #7dbb3c;
    --balloon-green: #9fcf78;
    --gear-grey: #c7ccd3;
  }
  * { margin: 0; padding: 0; box-sizing: border-box; }
  html, body { width: 954px; height: 1200px; overflow: hidden; background: #ffffff; }
  .invitation {
    position: relative;
    width: 954px;
    height: 1200px;
    overflow: hidden;
    font-family: "Oswald", sans-serif;
    color: var(--white);
  }
  .machinery-backdrop {
    position: absolute;
    inset: 0;
    background:
      radial-gradient(circle at 12% 20%, var(--steel-light) 0%, transparent 22%),
      radial-gradient(circle at 88% 35%, var(--steel-light) 0%, transparent 20%),
      radial-gradient(circle at 85% 85%, var(--steel-blue) 0%, transparent 28%),
      radial-gradient(circle at 15% 75%, var(--steel-mid) 0%, transparent 30%),
      linear-gradient(160deg, var(--steel-mid) 0%, var(--steel-dark) 45%, var(--steel-blue) 75%, var(--steel-dark) 100%);
  }
  .info-panel {
    position: absolute;
    top: 0;
    left: 207px;
    width: 550px;
    height: 1200px;
    background: var(--navy);
    text-align: center;
  }
  .headline {
    position: absolute;
    left: 0; right: 0;
    font-weight: 500;
    text-transform: uppercase;
    letter-spacing: 1px;
  }
  .headline--intro { top: 78px; font-size: 40px; }
  .headline--opening { top: 150px; font-size: 44px; }
  .headline--opening .lowercase { text-transform: none; }
  .brand-name {
    position: absolute;
    left: 0; right: 0;
    top: 300px;
    display: flex;
    flex-direction: column;
    align-items: center;
  }
  .brand-name__square {
    width: 70px;
    height: 70px;
    background: var(--accent-green);
    margin-bottom: 40px;
  }
  .brand-name__text {
    font-size: 78px;
    line-height: 1.05;
    font-weight: 600;
    color: var(--name-grey);
    letter-spacing: 4px;
    text-transform: uppercase;
  }
  .event-date {
    position: absolute;
    left: 0; right: 0;
    top: 668px;
    font-size: 44px;
    font-weight: 500;
  }
  .venue {
    position: absolute;
    left: 0; right: 0;
    top: 762px;
    font-size: 38px;
    font-weight: 500;
    line-height: 1.5;
  }
  .dinner-note {
    position: absolute;
    left: 0; right: 0;
    top: 910px;
    font-size: 27px;
    font-weight: 500;
    letter-spacing: 1.5px;
    text-transform: uppercase;
  }
  .balloons {
    position: absolute;
    left: 195px;
    top: 990px;
    width: 160px;
    height: 160px;
    border-radius: 50%;
    background: radial-gradient(circle, var(--balloon-green) 0%, rgba(159,207,120,0.4) 50%, transparent 72%);
  }
  .gear-mark {
    position: absolute;
    top: 1128px;
    width: 80px;
    height: 34px;
    border-radius: 17px;
    background: radial-gradient(ellipse, var(--gear-grey) 0%, rgba(199,204,211,0.5) 55%, transparent 75%);
  }
  .gear-mark--left { left: 70px; }
  .gear-mark--right { right: 70px; }
</style>
</head>
<body>
  <main class="invitation">
    <div class="machinery-backdrop" role="img" aria-label="Close-up photograph of steel gears and machinery in cool blue tones"></div>

    <section class="info-panel">
      <p class="headline headline--intro">Join us to celebrate</p>
      <p class="headline headline--opening"><span class="lowercase">the</span> Official Opening <span class="lowercase">of</span></p>

      <div class="brand-name">
        <span class="brand-name__square"></span>
        <span class="brand-name__text">Harlow<br>Ironworks</span>
      </div>

      <p class="event-date">Friday, August 26th, 6pm</p>
      <p class="venue">Venue Name<br>5678 Road label</p>
      <p class="dinner-note">Light dinner provided</p>

      <div class="gear-mark gear-mark--left" role="img" aria-label="Small decorative gear cluster"></div>
      <div class="balloons" role="img" aria-label="Illustration of a bunch of green balloons"></div>
      <div class="gear-mark gear-mark--right" role="img" aria-label="Small decorative gear cluster"></div>
    </section>
  </main>
</body>
</html>
```